Custom Software Solutions

web design for a small custom programming company in Brisbane Australia. Specialize in business finance solutions, OfficeDesk automation and programming and data analysis. The design should portray professionalism and honesty. Main applications deal with financial accounting reporting and analysis. Would like to see colors blue and purple used (but sparsely). added file is company logo. Trading name is TR Solutions, while the official company name is TR Solutions (QLD) Pty Ltd.

Target Market(s)

current clients for support
marketing tool for prospective clients

Industry/Entity Type

Business

Number of Pages Required

5+ page

Font styles to use
Sans Serif

Colors
0555a3
a54599
ffffff

Requirements
Must have
• introduction
• blog for news and tips
• previous and current clients/projects page
• contact us page with email submission form
Should not have
• social media links

```html
<!DOCTYPE html>
<html lang="en">
<head>
<meta charset="utf-8">
<title>TR Solutions – Custom Software Solutions</title>
<link href="https://fonts.googleapis.com/css2?family=Open+Sans:wght@400;600&display=swap" rel="stylesheet">
<style>
  :root {
    --blue: #0555a3;
    --purple: #a54599;
    --purple-light: #b655ab;
    --purple-dark: #97378b;
    --white: #ffffff;
    --page-grey: #f4f4f4;
    --text-grey: #777777;
    --logo-grey: #8a8a8a;
    --footer-dark: #2b2b2b;
    --footer-text: #a6a6a6;
    --border: #e2e2e2;
  }
  * { box-sizing: border-box; margin: 0; padding: 0; }
  html, body { width: 1200px; height: 1096px; overflow: hidden; }
  body {
    font-family: "Open Sans", Arial, sans-serif;
    background: var(--page-grey);
    color: var(--text-grey);
    position: relative;
  }
  .container { position: absolute; left: 99px; width: 1002px; }

  /* Header */
  .site-header { position: absolute; top: 0; left: 0; width: 1200px; height: 144px; background: var(--white); }
  .brand { position: absolute; left: 100px; top: 62px; display: flex; align-items: center; gap: 12px; }
  .brand-mark { width: 34px; height: 34px; border-radius: 50%; background: var(--blue); }
  .brand-name { font-size: 34px; font-weight: 400; color: var(--blue); letter-spacing: 1px; }
  .contact-block { position: absolute; right: 100px; top: 24px; text-align: right; }
  .contact-title { font-size: 18px; color: #888; line-height: 26px; }
  .contact-line { font-size: 13px; color: #999; line-height: 31px; }
  .contact-line .intl { font-size: 20px; color: var(--purple); }
  .contact-line .local { font-size: 20px; color: var(--blue); font-weight: 600; }

  /* Navigation */
  .main-nav {
    top: 144px; height: 50px;
    background: linear-gradient(var(--purple-light), var(--purple-dark));
    display: flex;
  }
  .main-nav a {
    display: flex; align-items: center; padding: 0 24px;
    color: var(--white); font-size: 14px; font-weight: 600; text-decoration: none;
    border-right: 1px solid rgba(0,0,0,0.15);
  }
  .main-nav a.active { background: linear-gradient(#1a68b8, var(--blue)); padding: 0 23px; }
  .search-box {
    position: absolute; right: 5px; top: 5px; width: 268px; height: 40px;
    background: var(--white); display: flex; align-items: center; justify-content: space-between;
    padding: 0 12px 0 15px; font-size: 13px; color: #999;
  }

  /* Hero */
  .hero { top: 194px; height: 393px; background: var(--white); border: 1px solid var(--border); border-top: none; }
  .hero-media {
    position: absolute; right: 0; top: 0; width: 590px; height: 392px;
    background: linear-gradient(90deg, rgba(255,255,255,1) 0%, #e8ebd4 30%, #c9cfa8 60%, #a5ab86 100%);
  }
  .hero-copy { position: absolute; left: 45px; top: 73px; width: 390px; }
  .hero-kicker { font-size: 25px; color: var(--purple); line-height: 30px; }
  .hero-title { font-size: 40px; color: var(--blue); font-weight: 600; line-height: 48px; }
  .hero-text { margin-top: 14px; font-size: 13.5px; line-height: 21px; color: var(--text-grey); }
  .slider-dots {
    position: absolute; left: 45px; top: 263px; width: 101px; height: 24px; border-radius: 12px;
    background: #7d7d7d; display: flex; align-items: center; justify-content: space-around; padding: 0 8px;
  }
  .slider-dots span { width: 11px; height: 11px; border-radius: 50%; background: var(--white); }
  .slider-dots span.current { background: #7d7d7d; border: 2px solid var(--white); }

  /* Services */
  .services { top: 618px; display: flex; justify-content: space-between; }
  .service { width: 320px; text-align: center; }
  .service-icon { width: 134px; height: 134px; border-radius: 50%; margin: 0 auto; }
  .service-icon.finance { background: #4f5a74; }
  .service-icon.office { background: #0b72a8; }
  .service-icon.code { background: #e0955a; }
  .service h2 { margin-top: 17px; font-size: 21px; font-weight: 400; color: var(--blue); line-height: 30px; }
  .service p { margin-top: 6px; font-size: 13.5px; line-height: 21px; color: var(--text-grey); }

  /* Clients */
  .clients { position: absolute; top: 903px; left: 0; width: 1200px; height: 120px; background: var(--white); }
  .client-list {
    position: absolute; left: 112px; right: 112px; top: 44px; display: flex; justify-content: space-between; align-items: center;
  }
  .client-list span { font-size: 22px; color: var(--logo-grey); font-weight: 400; }

  /* Footer */
  .site-footer {
    position: absolute; top: 1023px; left: 0; width: 1200px; height: 73px; background: var(--footer-dark);
    display: flex; align-items: center; justify-content: center; font-size: 13.5px; color: var(--footer-text);
  }
</style>
</head>
<body>
  <header class="site-header">
    <div class="brand">
      <span class="brand-mark"></span>
      <span class="brand-name">TR Solutions</span>
    </div>
    <div class="contact-block">
      <div class="contact-title">Call us</div>
      <div class="contact-line">(international) <span class="intl">+61- 4 - 00000000</span></div>
      <div class="contact-line">(within Australia) <span class="local">0400 000 000</span></div>
    </div>
  </header>

  <nav class="container main-nav">
    <a class="active" href="#">HOME</a>
    <a href="#">ABOUT US</a>
    <a href="#">SERVICES</a>
    <a href="#">PROJECTS</a>
    <a href="#">CONTACT US</a>
    <div class="search-box">
      <span>Search</span>
      <svg width="17" height="17" viewBox="0 0 17 17" aria-hidden="true">
        <circle cx="7" cy="7" r="5.5" fill="none" stroke="#666" stroke-width="2"/>
        <line x1="11" y1="11" x2="15.5" y2="15.5" stroke="#666" stroke-width="2.2" stroke-linecap="round"/>
      </svg>
    </div>
  </nav>

  <section class="container hero">
    <div class="hero-media" role="img" aria-label="Photo of a person touching a screen overlaid with lines of program code"></div>
    <div class="hero-copy">
      <div class="hero-kicker">Welcome to</div>
      <h1 class="hero-title">TR Solutions</h1>
      <p class="hero-text">Nam molestie pulvinar diam. Duis ullamcorper efficitur mi eu ultricies. Donec fringilla nisl eu elit lobortis, venenatis gravida tortor porta. Nunc malesuada et est nec placerat. Suspend-isse efficitur cursus bibendum.</p>
    </div>
    <div class="slider-dots"><span class="current"></span><span></span><span></span><span></span></div>
  </section>

  <section class="container services">
    <article class="service">
      <div class="service-icon finance" role="img" aria-label="Banknote icon"></div>
      <h2>Business Finance Soutions</h2>
      <p>Cras quis diam gravida, lacinia turpis aliquet, congue tellus. Nulla euismod pharetra nisi vel interdum. dictum dui in diam.</p>
    </article>
    <article class="service">
      <div class="service-icon office" role="img" aria-label="Office software icon"></div>
      <h2>OfficeDesk Automation</h2>
      <p>Cras quis diam gravida, lacinia turpis aliquet, congue tellus. Nulla euismod pharetra nisi vel interdum. dictum dui in diam.</p>
    </article>
    <article class="service">
      <div class="service-icon code" role="img" aria-label="Keyboard icon"></div>
      <h2>Programming &amp; Data Analysis</h2>
      <p>Cras quis diam gravida, lacinia turpis aliquet, congue tellus. Nulla euismod pharetra nisi vel interdum. dictum dui in diam.</p>
    </article>
  </section>

  <section class="clients" aria-label="Clients">
    <div class="client-list">
      <span>Hartfield</span>
      <span>Brightlane</span>
      <span>Kestrel</span>
      <span>Norvale</span>
      <span>Tessaro</span>
      <span>Quorra</span>
      <span>Pellworth</span>
      <span>Arden</span>
      <span>Solvane</span>
    </div>
  </section>

  <footer class="site-footer">Copyright &nbsp;©&nbsp; 2014 &nbsp;TR Solutions.&nbsp;&nbsp; All rights reserved.</footer>
</body>
</html>
```